Bolts & Burdens: Mending What Lies Beneath

AUTHORS BIO:
Wade Pemberton is a 20-year Northern Union Aerial Corps veteran who served as a Crew Chief for K-37 and K-48 fighter jets, maintaining the backbone of America’s air superiority through multiple deployments to Afghanistan and other austere locations. Shaped by the loss of his father as a young adult and the lingering scars of childhood trauma, he confronts PTSD with the same tenacity he brought to the flightline. A survivor and advocate, he brings a raw, hard-earned perspective to "Bolts and Burdens," blending the grit of a serviceman with the insight of a man determined to heal. Focused on helping men confront their pain and find strength in vulnerability. Wade now lives in Jacksonville, North Carolina, where he continues to advocate for those shaped by trauma’s lasting weight.

SUMMARY:
In this raw and revealing non-fiction work, Wade Pemberton delves into the lasting echoes of childhood trauma and its profound impact on adult life, with a lens on his 20-year career in the Aerial Corps. Blending personal experience with hard-earned insight, the book explores how post-traumatic stress disorder (PTSD) shapes the mind and body, often in ways that remain hidden until the pressure builds beyond breaking points. With a focus on men—who are too often taught to bury their pain—this narrative offers a roadmap to understanding, confronting, and healing from the torque of trauma. Written in a direct, unflinching voice, "Bolts and Burdens" is both a memoir of resilience and a call to action for those ready to face the past to reclaim their future. Thank you for joining me on this adventure called life. It means more to me than you will ever know.

Target Market(s)

Those serving in the military and post military life with an emphasis on trauma

Font styles to use
Serif

Requirements
Must have
• NUAC K-37 or K-48 aircraft, NO AI GENERATED AIRCRAFT please
Nice to have
• An American Flag
Should not have
• AI generated aircraft

```html
<!DOCTYPE html>
<html lang="en">
<head>
<meta charset="utf-8">
<title>Bolts &amp; Burdens — Cover Spread</title>
<link rel="stylesheet" href="https://fonts.googleapis.com/css2?family=Anton&family=Montserrat:wght@400;500&family=Oswald:wght@500&display=swap">
<style>
  :root{
    --surround:#6b6b6b;
    --back-blue:#bfe0f7;
    --front-blue:#3a93e0;
    --front-blue-light:#5aa8ea;
    --navy:#1d1b30;
    --band-navy:#0e1233;
    --red:#c51f31;
    --text:#1e2030;
    --amp:#e9e6e4;
    --rule-navy:#1d2145;
    --rule-red:#b3202f;
    --sky-pale:#d6e7f4;
    --tarmac:#8c9094;
    --jet-grey:#4d5560;
  }
  *{box-sizing:border-box;margin:0;padding:0}
  html,body{width:1200px;height:858px;overflow:hidden;background:var(--surround)}
  .spread{position:absolute;left:11px;top:14px;width:1177px;height:830px;}
  .back-cover{position:absolute;left:0;top:0;width:554px;height:830px;background:var(--back-blue);border-right:1px solid #aed3ee}
  .spine{position:absolute;left:554px;top:0;width:70px;height:830px;background:var(--back-blue)}
  .front-cover{position:absolute;left:624px;top:0;width:553px;height:830px;background:var(--front-blue);overflow:hidden}
  .svg-layer{position:absolute;left:0;top:0}
  .summary{position:absolute;left:36px;top:166px;width:482px;font:400 12.6px/15.4px "Montserrat",sans-serif;color:var(--text);text-align:justify;hyphens:auto}
  .author-rule{position:absolute;left:36px;top:356px;width:482px;display:flex;align-items:center;gap:5px}
  .author-rule .line{flex:1;height:1px;background:linear-gradient(90deg,var(--rule-navy),var(--rule-red))}
  .author-rule .name{font:500 21px/24px "Montserrat",sans-serif;color:var(--rule-navy);letter-spacing:.5px}
  .bio{position:absolute;left:36px;top:398px;width:482px;font:400 12.6px/15.4px "Montserrat",sans-serif;color:var(--text);text-align:justify;hyphens:auto}
  .author-photo{float:left;width:187px;height:209px;margin:-4px 8px 3px 0;background:linear-gradient(135deg,#c9d9e8 0%,#8fb0cf 45%,#1f2a4a 100%)}
  .cover-photo{position:absolute;left:0;top:372px;width:553px;height:395px;
    background:
      radial-gradient(ellipse 46% 30% at 50% 72%,rgba(77,85,96,.85) 0%,rgba(77,85,96,.35) 55%,rgba(77,85,96,0) 100%),
      linear-gradient(180deg,var(--front-blue) 0%,#7db6e6 25%,var(--sky-pale) 62%,#c4ccd2 79%,var(--tarmac) 82%,#7d8185 100%)}
  .author-band{position:absolute;left:0;top:767px;width:553px;height:63px;background:var(--band-navy);display:flex;align-items:center;justify-content:center}
  .author-band .name{font:500 40px/1 "Montserrat",sans-serif;color:#fff;letter-spacing:1.5px}
</style>
</head>
<body>
<div class="spread">

  <section class="back-cover">
    <svg class="svg-layer" width="554" height="170" aria-label="Bolts &amp; Burdens">
      <defs>
        <linearGradient id="back-burden" x1="0" y1="0" x2="0" y2="1">
          <stop offset="0" stop-color="#2a1c2c"/><stop offset="1" stop-color="#c51f31"/>
        </linearGradient>
      </defs>
      <text x="187" y="87" font-family="Anton, sans-serif" font-size="58" fill="#1d1b30" textLength="180" lengthAdjust="spacingAndGlyphs">BOLTS</text>
      <text x="187" y="151" font-family="Anton, sans-serif" font-size="57" fill="url(#back-burden)" textLength="180" lengthAdjust="spacingAndGlyphs">BURDENS</text>
      <text x="277" y="112" text-anchor="middle" font-family="Anton, sans-serif" font-size="42" fill="#e9e6e4" opacity=".92">&amp;</text>
    </svg>

    <p class="summary">In this raw and revealing non-fiction work, Wade Pemberton delves into the lasting echoes of childhood trauma and its profound impact on adult life, with a lens on his 20-year career in the Aerial Corps. Blending personal experience with hard-earned insight, the book explores how post-traumatic stress disorder (PTSD) shapes the mind and body, often in ways that remain hidden until the pressure builds beyond breaking points. With a focus on men—who are too often taught to bury their pain—this narrative offers a roadmap to understanding, confronting, and healing from the torque of trauma. Written in a direct, unflinching voice, "Bolts and Burdens" is both a memoir of resilience and a call to action for those ready to face the past to reclaim their future. Thank you for joining me on this adventure called life. It means more to me than you will ever know.</p>

    <div class="author-rule"><span class="line"></span><span class="name">WADE PEMBERTON</span><span class="line"></span></div>

    <div class="bio">
      <div class="author-photo" role="img" aria-label="Formal portrait of the author in dress uniform before a flag"></div>
      Wade Pemberton is a 20-year Northern Union Aerial Corps veteran who served as a Crew Chief for K-37 and K-48 fighter jets, maintaining the backbone of America’s air superiority through multiple deployments to Afghanistan and other austere locations. Shaped by the loss of his father as a young adult and the lingering scars of childhood trauma, he confronts PTSD with the same tenacity he brought to the flightline. A survivor and advocate, he brings a raw, hard-earned perspective to "Bolts and Burdens," blending the grit of a serviceman with the insight of a man determined to heal. Focused on helping men confront their pain and find strength in vulnerability. Wade now lives in Jacksonville, North Carolina, where he continues to advocate for those shaped by trauma’s lasting weight.
    </div>
  </section>

  <section class="spine">
    <svg class="svg-layer" width="70" height="830" aria-label="Bolts &amp; Burdens by Wade Pemberton">
      <text transform="translate(13,35) rotate(90)" font-family="Anton, sans-serif" font-size="62" textLength="366" lengthAdjust="spacingAndGlyphs"><tspan fill="#1d1b30">BOLTS </tspan><tspan fill="#1d1b30">&amp; </tspan><tspan fill="#c51f31">BURDENS</tspan></text>
      <text transform="translate(22,503) rotate(90)" font-family="Montserrat, sans-serif" font-weight="500" font-size="39" fill="#1d2145" textLength="283" lengthAdjust="spacingAndGlyphs">WADE PEMBERTON</text>
    </svg>
  </section>

  <section class="front-cover">
    <div class="cover-photo" role="img" aria-label="Photograph: waving flag in the sky above a twin-engine K-37 fighter jet parked on the flightline, seen from behind"></div>
    <svg class="svg-layer" width="553" height="420" aria-label="Bolts &amp; Burdens: Mending What Lies Beneath">
      <defs>
        <linearGradient id="front-burden" x1="0" y1="0" x2="0" y2="1">
          <stop offset="0" stop-color="#2a1c2c"/><stop offset="1" stop-color="#c51f31"/>
        </linearGradient>
      </defs>
      <text x="34" y="177" font-family="Anton, sans-serif" font-size="160" fill="#1d1b30" textLength="484" lengthAdjust="spacingAndGlyphs">BOLTS</text>
      <text x="35" y="343" font-family="Anton, sans-serif" font-size="153" fill="url(#front-burden)" textLength="481" lengthAdjust="spacingAndGlyphs">BURDENS</text>
      <text x="275" y="244" text-anchor="middle" font-family="Anton, sans-serif" font-size="117" fill="#e9e6e4" opacity=".92">&amp;</text>
      <text x="63" y="404" font-family="Oswald, sans-serif" font-weight="500" font-size="40" fill="#ffffff" textLength="455" lengthAdjust="spacingAndGlyphs">MENDING WHAT LIES BENEATH</text>
    </svg>
    <div class="author-band"><span class="name">WADE PEMBERTON</span></div>
  </section>

</div>
</body>
</html>
```